Adult Literacy Program - flyer to attract volunteers and students

We want a flyer that is engaging, colorful, modern and will appeal to our primary audience of adults aged 40-60. We are trying to attract both prospective volunteers (typically age 50+, mostly women) and students (typically aged 40+).
The flyer should feature diverse people working together in pairs of two, reading or talking, with a workbook or some reading material in front of them.

Our organization trains tutors to work one-on-one with adults who are learning how to read. Most of our adult students are non-native speakers of English. Many are of Haitian or Hispanic origin, so we would like some people who represent that demographic.

The Flyer should represent reading, learning, literacy, knowledge, growth,
and opportunities.
Our students are learning to read so they can advance their job opportunities.

Target Market(s)

Adults aged 40-60, primarily women, retired, volunteers

Industry/Entity Type

Education

Font styles to use
Serif
Sans Serif

Colors

Designer to choose colors to be used in the design.

Requirements
Must have
• - UPDATE: Should be designed as a TRI-FOLD brochure on 8.5 x 11 inch paper that will be folded into thirds.
• - Images of diverse people, women and men, who look Hispanic, Haitian and other nationalities as well as Caucasian.
• - Our logo on the front cover
Nice to have
• The sample flyer is very boring and dry! We are open to different ways of presenting the text.

```html
<!DOCTYPE html>
<html lang="en">
<head>
<meta charset="utf-8">
<title>Adult Literacy Tri-fold Brochure</title>
<link href="https://fonts.googleapis.com/css2?family=Open+Sans:wght@400;600;700&display=swap" rel="stylesheet">
<style>
  :root {
    --stage: #2b2b2b;
    --paper: #ffffff;
    --sky: #5ec8e8;
    --sun: #ffdd00;
    --lemon: #fff200;
    --leaf: #6cc07a;
    --leaf-text: #7cc576;
    --ink-blue: #3a73b0;
    --photo-cool: #8aa5b4;
  }
  * { box-sizing: border-box; margin: 0; padding: 0; }
  html, body { width: 1200px; height: 1200px; overflow: hidden; background: var(--stage); }
  body { position: relative; font-family: "Open Sans", Arial, sans-serif; color: var(--ink-blue); }
  .sheet { position: absolute; left: 238px; width: 725px; background: var(--paper); overflow: hidden; }
  .sheet--outside { top: 34px; height: 560px; }
  .sheet--inside { top: 617px; height: 568px; }
  .sheet svg.backdrop { position: absolute; left: 0; top: 0; width: 725px; height: 100%; }
  .abs { position: absolute; }
  .photo { position: absolute; }
  .photo--warm { background: linear-gradient(135deg, #c9a27c, #7d5d43); }
  .photo--library { background: linear-gradient(135deg, #9c6a45, #d7b48a 55%, #6d4a30); }
  .frame { position: absolute; border-radius: 26px; }
  .frame--sun { background: var(--sun); }
  .frame--lemon { background: var(--lemon); }
  .frame__photo { position: absolute; border-radius: 14px; }
  .headline { position: absolute; font-weight: 400; line-height: 1; white-space: nowrap; }
  .headline--white { color: #fff; }
  .headline--blue { color: var(--ink-blue); }
  .headline--green { color: var(--leaf-text); text-align: center; }
  .copy { position: absolute; font-size: 13px; line-height: 15.4px; text-align: center; }
  .brand { position: absolute; display: flex; align-items: center; justify-content: center; gap: 6px; font-weight: 700; color: var(--ink-blue); }
  .brand__dot { width: 16px; height: 16px; border-radius: 50%; background: var(--sky); flex: none; }
  .web { position: absolute; font-size: 13px; }
  .bullets { position: absolute; left: 26px; top: 233px; width: 165px; font-size: 17px; line-height: 20px; list-style: none; }
  .contact { position: absolute; font-size: 13px; line-height: 15.5px; white-space: nowrap; }
  .contact--center { text-align: center; }
  .badge { position: absolute; background: var(--paper); display: flex; align-items: center; justify-content: center; }
</style>
</head>
<body>

<section class="sheet sheet--outside">
  <svg class="backdrop" viewBox="0 0 725 560" aria-hidden="true">
    <path d="M0 0 H622 C560 55 440 95 310 94 C260 95 240 120 200 150 C150 185 70 180 0 170 Z" fill="var(--sky)"/>
    <path d="M250 106 C420 120 560 100 625 30 C580 90 450 120 248 115 Z" fill="var(--sun)"/>
    <path d="M0 176 C90 186 170 180 225 135 C180 185 90 198 0 186 Z" fill="var(--sun)"/>
    <path d="M464 560 C520 470 620 460 725 462 V560 Z" fill="var(--sky)"/>
    <path d="M510 505 C560 460 650 450 725 448 V454 C650 456 570 470 510 505 Z" fill="var(--sun)"/>
  </svg>

  <div class="headline headline--white" style="left:16px;top:54px;font-size:46px;">Volunteer</div>
  <div class="headline headline--white" style="left:298px;top:30px;font-size:44px;">Tutors</div>

  <div class="photo photo--warm" style="left:0;top:150px;width:242px;height:184px;" role="img" aria-label="Photo of two women studying together at a table"></div>
  <div class="photo photo--library" style="left:244px;top:160px;width:237px;height:173px;" role="img" aria-label="Photo of a tutor and an older man reading together in a library"></div>

  <div class="frame frame--sun" style="left:514px;top:102px;width:210px;height:273px;"></div>
  <div class="frame__photo" style="left:550px;top:138px;width:140px;height:216px;background:linear-gradient(160deg,var(--sky),var(--photo-cool));" role="img" aria-label="Photo of an older man smiling while holding an open book"></div>
  <div class="headline headline--blue" style="left:534px;top:60px;font-size:44px;">Students</div>

  <div class="headline headline--blue" style="left:0;width:262px;text-align:center;top:348px;font-size:32px;">Enrich a Life!</div>
  <div class="copy" style="left:0;width:262px;top:396px;font-size:17px;line-height:20px;">Help an adult to read,<br>write or speak English</div>

  <div class="brand" style="left:0;width:262px;top:512px;font-size:14px;"><span class="brand__dot"></span>Open Page Literacy Friends</div>

  <div class="copy" style="left:254px;width:220px;top:357px;">
    No special skills or degrees<br>needed — just a degree of caring!<br>Training offered throughout the<br>year<br>Tutors meet students weekly at a<br>library<br>Instructional materials provided<br>Ongoing support available
  </div>
  <div class="copy" style="left:244px;width:240px;top:510px;line-height:20px;">Teach an adult to read and you'll<br>change a life forever.</div>

  <div class="copy" style="left:524px;top:383px;width:190px;text-align:left;">Students are adults in need of basic literacy skilpre GED skills conversational English</div>
  <div class="web" style="left:554px;top:528px;color:#fff;">WWW.harborreads.org</div>
</section>

<section class="sheet sheet--inside">
  <svg class="backdrop" viewBox="0 0 725 568" aria-hidden="true">
    <path d="M0 0 H640 C580 60 450 100 310 98 C260 100 240 125 200 155 C150 195 70 180 0 178 Z" fill="var(--lemon)"/>
    <path d="M255 108 C420 125 580 100 640 0 C600 90 450 130 252 117 Z" fill="var(--leaf)"/>
    <path d="M0 184 C90 200 180 190 233 138 C190 195 90 212 0 196 Z" fill="var(--leaf)"/>
    <path d="M140 568 C220 470 380 460 502 465 C560 430 640 405 725 400 V568 Z" fill="var(--lemon)"/>
    <path d="M140 568 C220 468 380 452 506 462 V468 C380 460 230 470 140 568 Z" fill="var(--leaf)"/>
    <path d="M528 375 C580 345 650 375 725 378 V386 C650 382 590 360 528 375 Z" fill="var(--leaf)"/>
  </svg>

  <div class="headline headline--green" style="left:0;width:240px;top:14px;font-size:34px;line-height:40px;">Connect<br>Inspire<br>Enrich</div>
  <div class="headline headline--green" style="left:218px;width:300px;top:14px;font-size:34px;line-height:40px;">Don’t waste a<br>moment!</div>

  <div class="frame frame--lemon" style="left:514px;top:90px;width:210px;height:277px;"></div>
  <div class="frame__photo" style="left:550px;top:127px;width:140px;height:216px;background:linear-gradient(160deg,var(--leaf),#8a7a8c);" role="img" aria-label="Photo of an older woman and a younger woman reading a worksheet together"></div>

  <ul class="bullets">
    <li>•basic literacy skills</li>
    <li>•pre-GED skills</li>
    <li>•conversational English</li>
    <li>•Tutoring is free of charge</li>
    <li>• Tutoring is one-on-one</li>
    <li>• Flexible scheduling during library hours</li>
    <li>• Lessons focus on student goals</li>
  </ul>

  <div class="contact contact--center" style="left:268px;width:200px;top:245px;">Contact us today<br>to learn more.</div>

  <div class="contact contact--center" style="left:278px;width:200px;top:289px;">Volunteer Desk</div>
  <svg class="abs" style="left:304px;top:302px;" width="16" height="16" viewBox="0 0 24 24" aria-hidden="true"><path fill="var(--leaf)" d="M6.6 10.8a15 15 0 0 0 6.6 6.6l2.2-2.2c.3-.3.7-.4 1-.2 1.1.4 2.3.6 3.6.6.6 0 1 .4 1 1V20c0 .6-.4 1-1 1A17 17 0 0 1 3 4c0-.6.4-1 1-1h3.5c.6 0 1 .4 1 1 0 1.3.2 2.5.6 3.6.1.3 0 .7-.2 1z"/></svg>
  <div class="contact" style="left:328px;top:305px;">555-010-7510</div>

  <svg class="abs" style="left:305px;top:332px;" width="12" height="18" viewBox="0 0 12 18" aria-hidden="true"><path fill="var(--leaf)" d="M6 0a6 6 0 0 1 6 6c0 4.5-6 12-6 12S0 10.5 0 6a6 6 0 0 1 6-6zm0 3.5a2.5 2.5 0 1 0 0 5 2.5 2.5 0 0 0 0-5z"/></svg>
  <div class="contact contact--center" style="left:322px;width:152px;top:336px;">Cedar Glen, Lakeview &amp;<br>South Point</div>
  <svg class="abs" style="left:304px;top:365px;" width="16" height="16" viewBox="0 0 24 24" aria-hidden="true"><path fill="var(--leaf)" d="M6.6 10.8a15 15 0 0 0 6.6 6.6l2.2-2.2c.3-.3.7-.4 1-.2 1.1.4 2.3.6 3.6.6.6 0 1 .4 1 1V20c0 .6-.4 1-1 1A17 17 0 0 1 3 4c0-.6.4-1 1-1h3.5c.6 0 1 .4 1 1 0 1.3.2 2.5.6 3.6.1.3 0 .7-.2 1z"/></svg>
  <div class="contact" style="left:328px;top:368px;">555-010-3453</div>

  <div class="contact contact--center" style="left:245px;width:240px;top:405px;">email: literacy@harborreads.org</div>

  <div class="badge" style="left:318px;top:479px;width:110px;height:82px;">
    <div class="brand" style="position:static;font-size:11px;flex-direction:column;text-align:center;gap:4px;"><span class="brand__dot" style="background:var(--sun);"></span>Harbor County Library</div>
  </div>
  <div class="badge" style="left:553px;top:439px;width:166px;height:120px;">
    <div class="brand" style="position:static;font-size:13px;flex-direction:column;text-align:center;gap:5px;"><span class="brand__dot"></span>Open Page<br>Literacy Friends</div>
  </div>

  <div class="web" style="left:10px;top:540px;color:var(--leaf-text);">www.harborreads.org</div>
</section>

</body>
</html>
```